Refinery Service Website (Wholesale) – Luxurious Landing Pages & Industry Hub

We are seeking talented designers to create a luxurious and professional redesign for the wholesale section of our refinery service website, Steadfast KLV. Our current refinery page (https://steadfastklv.com/refinery/) and dental landing page (https://steadfastklv.com/refinery/dental-gold/) provide functional starting points with existing content (words, sections, trust badges, and video placeholders) that must be retained and enhanced with a sophisticated, high-end aesthetic. We serve high-net-worth wholesale clients across industries such as dental practices, mortuaries, estate attorneys, dentists, pawnshops, jewelry stores, and financial advisors. The project includes designing a revamped main wholesale landing page, individual landing pages for each industry with specific sections, and a central hub page to showcase these industries in an SEO-friendly and user-focused way, all while elevating the design to a luxurious standard.

Project Overview
Our refinery service specializes in precious metals and serves a variety of industries through wholesale access. We want the wholesale section of our website to exude sophistication and exclusivity while preserving and enhancing the existing content on our pages. Currently:
• Our refinery page (https://steadfastklv.com/refinery/) provides a basic overview of our services with text, sections, and trust badges, but it lacks visual appeal and a high-end feel.
• Our dental landing page (https://steadfastklv.com/refinery/dental-gold/) targets dental professionals with relevant messaging, sections, and content, but it also feels utilitarian and could benefit from a more elegant design, improved layout, and stronger calls-to-action.
Designers must use the existing words, sections, trust badges, and video placeholders from these pages as a foundation, enhancing them with a luxurious redesign and adding the additional sections specified below. We admire the clean and professional look of https://www.brovelmetalworks.com/, but we aim to elevate our design with a more luxurious and exclusive feel to attract discerning wholesale clients. The redesign will involve:
1 Main Wholesale Landing Page: A complete overhaul of our current refinery page into a luxurious and professional entry point, retaining and enhancing existing content while improving the overall design.
2 Industry-Specific Landing Pages: A dedicated landing page for each of the following industries: dental practices, mortuaries, estate attorneys, dentists, pawnshops, jewelry stores, and financial advisors. Each page must retain and enhance existing content (where applicable) and include specific sections (detailed below) to build trust, provide information, and encourage engagement.
3 Industry Hub Page: A central page that showcases all the industries we serve in a visually appealing and SEO-optimized manner, acting as a gateway to each industry-specific landing page.
Our website is built on WordPress using the Tiles Composer, so design submissions should be provided in HTML, CSS, or as a Figma file for seamless integration. The design must be responsive, visually striking, and optimized for usability across all devices (desktop, tablet, mobile).
Project Scope
We are looking for design submissions that include:
• Main Wholesale Landing Page: A redesigned version of our current refinery page (https://steadfastklv.com/refinery/), transformed into a luxurious and professional entry point for our wholesale services. The new design must retain the existing words, sections, trust badges, and any video placeholders, enhancing them with a high-end aesthetic while improving layout and engagement.
• Industry-Specific Landing Pages: A dedicated landing page for each of the following industries: dental practices, mortuaries, estate attorneys, dentists, pawnshops, jewelry stores, and financial advisors. Each page must:
◦ Retain and enhance existing content (words, sections, trust badges, video placeholders) from pages like our dental landing page (https://steadfastklv.com/refinery/dental-gold/) as a reference, adapting it for each industry. For industries without existing pages, mirror the structure and content style of the dental page while tailoring the messaging and visuals.
◦ Include the following additional sections to enhance functionality and trust:
Trust Badges: A section displaying trust signals (e.g., certifications, accreditations, years in business) to build credibility with visitors. Include placeholders for 4–6 badges/icons, enhancing any existing badges from our current pages.
Testimonials: A section featuring 3–5 customer testimonials with placeholders for quotes, names, and industries (e.g., “Dr. Colm Varga, Dental Practice Owner”). If testimonials exist on current pages, enhance their presentation.
Contact Information: A clearly visible section with contact details (e.g., phone number, email, address) styled to match the luxurious aesthetic, improving any existing contact info presentation.
Contact Fillout Form: A user-friendly form for inquiries, including fields for name, email, industry, and message, with a professional design that encourages submissions, enhancing any existing forms.
Shipping Information: A section detailing shipping instructions and processes (e.g., how to send materials for refining), presented clearly and concisely, building on any existing shipping details.
Summary Service Bullet Points: A concise list of 5–7 key services or benefits tailored to the specific industry (e.g., “Fast turnaround for dental scrap” for dental pages, “Secure handling for jewelry inventory” for jewelers), improving any existing bullet points.
Video: Shipping Instructions: A placeholder for a video explaining how to ship materials to us, styled with a play button and a luxurious frame, enhancing any existing video placeholders.
Video: How Our Refinery Works: A placeholder for a video detailing our refining process, designed to match the aesthetic of the page, enhancing any existing video placeholders.
Video: Who We Are: A placeholder for a video introducing our company and values, presented in an elegant and professional manner, enhancing any existing video placeholders.
◦ Include tailored messaging and design elements that resonate with the specific industry (e.g., dental tools and scrap refining benefits for dental pages, elegant estate visuals for attorneys, jewelry displays for jewelers).
◦ Maintain a cohesive design that ties back to the overall luxurious aesthetic of the wholesale section.
• Industry Hub Page: A central hub page that showcases all the industries we serve in an SEO-friendly and visually engaging way. This page should include:
◦ A grid, carousel, or categorized layout featuring each industry with a concise description or tagline (e.g., “Dental Practices: Turn Scrap into Profit”).
◦ Links to each industry-specific landing page for easy navigation.
◦ Design elements that encourage exploration (e.g., hover effects, icons, or visuals representing each industry).
◦ SEO optimization through keyword-rich headings, meta-friendly layouts, and content areas that naturally incorporate industry terms.
• SEO and User Engagement Focus: The design should balance aesthetics with functionality, ensuring that both the hub page and individual landing pages are optimized for search engines (e.g., through clear headings, meta-friendly layouts) and capture user attention with compelling calls-to-action (e.g., “Discover Refinery Solutions for Your Dental Practice” or “Maximize Value for Your Jewelry Inventory”).
Design Requirements
• Aesthetic: Luxurious, elegant, and professional, with a focus on high-net-worth wholesale clients. The current designs (https://steadfastklv.com/refinery/ and https://steadfastklv.com/refinery/dental-gold/) are too basic and functional; we want a high-end look that conveys prestige and trust, using elements like deep golds, silvers, blacks, or whites to evoke luxury while enhancing existing content.
• Typography: Clean, modern, and sophisticated fonts that enhance readability and align with a high-end brand image, improving upon existing typography.
• Imagery: Incorporate placeholders for high-quality imagery relevant to each industry (e.g., dental tools, jewelry displays, legal documents). No stock images required in submissions—just placeholders. Retain and enhance any existing imagery placeholders from our current pages.
• Video Placeholders: Video sections (for shipping instructions, how the refinery works, and who we are) should include placeholders with play buttons and elegant frames that match the luxurious aesthetic, enhancing any existing video placeholders on our current pages.
• Responsiveness: The design must be fully responsive and look great on desktop, tablet, and mobile devices.
• SEO Optimization: The layout should support SEO best practices, such as clear heading structures (H1, H2, etc.), alt-text-friendly image placeholders, and keyword-rich content areas for each industry, building on existing content for SEO purposes.
• Deliverables Format: Submissions should include design files in HTML, CSS, or Figma format, ready for integration into WordPress with Tiles Composer.

Submission Guidelines
We invite designers to submit their concepts based on the following:
• A mockup of the redesigned main wholesale landing page, improving upon our current refinery page (https://steadfastklv.com/refinery/), retaining and enhancing existing words, sections, trust badges, and video placeholders with a luxurious aesthetic.
• A mockup of the industry hub page showcasing all the industries we serve (dental practices, mortuaries, estate attorneys, dentists, pawnshops, jewelry stores, financial advisors).
• At least two examples of industry-specific landing pages (e.g., one for dental practices, improving upon our current dental page (https://steadfastklv.com/refinery/dental-gold/), and one for jewelry stores), showing how the design retains and enhances existing content, incorporates all required sections (trust badges, testimonials, contact info, contact form, shipping info, service bullet points, and video placeholders), and tailors messaging to each audience.
• A brief explanation of your design choices, including how they enhance SEO, tailor messaging for each industry, incorporate and enhance existing content, include the required sections, and align with the luxurious and professional aesthetic we’re seeking.
• Files in HTML, CSS, or Figma format to demonstrate how the design can be implemented.

Judging Criteria
Submissions will be evaluated based on:
• Alignment with the luxurious and professional aesthetic described, significantly improving upon our current designs (https://steadfastklv.com/refinery/ and https://steadfastklv.com/refinery/dental-gold/) while retaining and enhancing existing content.
• Effective retention and enhancement of existing words, sections, trust badges, and video placeholders from our current pages, seamlessly integrating them into the new design.
• Inclusion and effective design of all required sections (trust badges, testimonials, contact info, contact form, shipping info, service bullet points, and video placeholders) on the industry-specific landing pages.
• Creativity and effectiveness in tailoring messaging and visuals for each industry-specific landing page.
• Usability and visual appeal of the industry hub page, including its potential to improve SEO and engage users.
• Suitability for the target audience (high-net-worth wholesale clients in dental, mortuary, legal, pawnshop, jewelry, and financial sectors).
• Compatibility with WordPress and Tiles Composer (based on the format of deliverables).

Additional Notes
• We are open to creative interpretations of “luxury” and encourage designers to think outside the box while maintaining professionalism. Use our current pages as a foundation for content and structure, enhancing and building upon them rather than replacing them entirely.
• The industry hub page should feel intuitive and encourage exploration, potentially using layouts like a grid, carousel, or categorized sections with hover effects.
• Each industry-specific landing page should include a unique value proposition (e.g., “Streamline Your Dental Scrap Refining Process” or “Maximize Value for Your Jewelry Inventory”) to capture attention, building on the clarity of our current dental page but with a more luxurious presentation and all required sections.
• We will provide feedback during the contest and may request revisions from top submissions.

About Us
Steadfast KLV is a leading refinery service provider specializing in precious metals, offering wholesale solutions to a wide range of industries such as dental, jewelry, and legal sectors. Our goal is to create a luxurious online presence that reflects the high value we provide to our clients.
We look forward to seeing your creative designs and how you can bring our vision of a luxurious, industry-focused wholesale section to life!

```html
<!DOCTYPE html>
<html lang="en">
<head>
<meta charset="utf-8">
<title>Refinery Process – Steadfast Precious Metals Refineries</title>
<link href="https://fonts.googleapis.com/css2?family=Montserrat:wght@600;700;800&family=Figtree:wght@400;500;600;700&display=swap" rel="stylesheet">
<style>
:root{
  --gold:#98720e;
  --gold-dark:#7c5c08;
  --ink:#161616;
  --text:#3a3a3a;
  --muted:#7a7a7a;
  --line:#cfcfcf;
  --paper:#ffffff;
  --soft:#f4f4f4;
  --panel:#f0f0f0;
  --night:#1b191a;
  --night-2:#121112;
  --navy:#1f2a6b;
  --blue:#4b5cd6;
  --red:#d6213b;
}
*{box-sizing:border-box;margin:0;padding:0}
html,body{width:1200px;height:3800px;overflow:hidden}
body{font-family:"Figtree",sans-serif;color:var(--text);background:var(--paper);position:relative}
h1,h2,h3{font-family:"Montserrat",sans-serif;color:var(--ink);font-weight:700}
.wrap{position:absolute;left:195px;width:812px}
.gold{color:var(--gold)}
.flourish{display:block;width:110px;height:4px;background:linear-gradient(90deg,transparent,var(--ink) 20%,var(--ink) 80%,transparent);border-radius:2px}

/* ticker */
.ticker{height:21px;background:#ececec;display:flex;justify-content:center;gap:26px;align-items:center;font-size:8px;color:#333}
.ticker b{font-weight:700;margin-right:4px}
.ticker .chg{display:inline-block;margin-left:4px;padding:0 3px;border:1px solid #d4b640;background:#f7eab0;border-radius:2px;font-size:7px}
.ticker .chg.down{border-color:#e07a7a;background:#f9d4d4}

/* header */
.header{height:41px;border-bottom:1px solid #ddd;position:relative}
.brand{position:absolute;left:195px;top:9px;display:flex;align-items:center;gap:8px;font-size:12px;letter-spacing:.5px;color:#222;text-transform:uppercase}
.brand i{width:22px;height:22px;border:1.5px solid #222;border-radius:50%}
.search{position:absolute;left:713px;top:8px;width:187px;height:25px;border:1px solid #bbb;border-radius:13px;font-size:7px;color:#888;padding:7px 12px}
.hicon{position:absolute;top:12px}
.call{position:absolute;left:977px;top:6px;width:30px;height:30px;border-radius:8px;background:var(--blue);display:grid;place-items:center}
.nav{height:25px;border-bottom:1px solid #ddd;display:flex;justify-content:space-between;padding:0 215px 0 232px;align-items:center;font-size:10px;font-weight:600;color:#222}

/* hero */
.hero{position:relative;height:336px;background:radial-gradient(circle at 52% 88%,#ffb13a 0,#e3621a 9%,#6d4a3a 20%,#474747 40%,#2c2c2c 100%)}
.hero h1{position:absolute;left:0;right:0;top:115px;text-align:center;color:#fff;font-size:46px;letter-spacing:1px;font-weight:800}
.hero .rule{position:absolute;left:355px;width:455px;height:3px;background:#fff}

/* trust */
.trust{height:134px;background:#fafafa;box-shadow:0 6px 10px rgba(0,0,0,.05);position:relative}
.trust h2{position:absolute;left:195px;top:33px;font-size:19px;line-height:22px;font-weight:800}
.trust .divider{position:absolute;left:387px;top:30px;width:2px;height:72px;background:#222}
.badge{position:absolute;top:30px;width:110px;text-align:center;font-size:10px;font-weight:700;color:#222}
.badge .shape{width:40px;height:44px;margin:0 auto 4px;background:#2a2a2a;border:3px solid #c9a43a;border-radius:50% 50% 45% 45%}
.badge small{display:block;font-size:6px;font-weight:400;color:#666}
.badge .square{width:88px;height:32px;margin:0 auto 4px;background:#2a2a2a;border-radius:3px}

/* about */
.about{position:absolute;top:582px;height:546px;left:0;width:1200px}
.video{position:absolute;left:195px;top:38px;width:362px;height:450px;border-radius:12px;background:linear-gradient(160deg,#b5b5b5,#a3a3a3)}
.play{position:absolute;left:50%;top:50%;width:62px;height:62px;margin:-31px;border-radius:50%;background:var(--red);display:grid;place-items:center}
.about .copy{position:absolute;left:597px;top:34px;width:410px}
.eyebrow{font-size:21px;font-weight:800}
.big{font-size:31px;line-height:37px;font-weight:800}
.copy p{font-size:11.6px;line-height:17.5px;text-align:justify;margin-top:15px;color:#333}

/* values */
.values{position:absolute;top:1132px;left:0;width:1200px;height:551px;background:var(--panel)}
.card{position:absolute;top:52px;width:252px;height:449px;background:#fafafa;border-radius:10px;box-shadow:0 6px 14px rgba(0,0,0,.08);overflow:hidden}
.card .photo{height:189px}
.card h3{font-size:14px;margin:25px 25px 14px;line-height:19px}
.card .flourish{margin:0 25px 20px;width:80px}
.card p{font-size:10.8px;line-height:17px;margin:0 25px;text-align:justify;color:#333}

/* relationships */
.rel{position:absolute;top:1683px;left:0;width:1200px;height:503px}
.rel .copy{position:absolute;left:195px;top:70px;width:410px}
.rel .copy p{font-size:11.6px;line-height:17.5px;text-align:justify;margin-top:15px;color:#333}
.rel .frame{position:absolute;left:651px;top:62px;width:356px;height:377px;background:linear-gradient(160deg,#f1f1f1,#e7e7e7);border-radius:8px}

/* registration */
.reg{position:absolute;top:2186px;left:0;width:1200px;height:567px;background:var(--panel)}
.center-title{text-align:center;font-size:26px;font-weight:800}
.reg .flourish,.testi .flourish{margin:18px auto 0}
.tabs{position:absolute;top:171px;left:223px;display:flex;gap:8px}
.tab{height:54px;border:1.5px solid #555;border-radius:27px;display:flex;align-items:center;gap:10px;padding:0 16px;font-size:10.5px;line-height:12px;color:#333;background:#fafafa}
.tab.active{background:var(--gold);border-color:var(--gold);color:#fff;font-weight:600}
.form{position:absolute;left:225px;top:253px;width:749px;height:261px;background:#fff;border-radius:10px;padding:36px 40px 0 40px;display:grid;grid-template-columns:repeat(3,215px);gap:14px 14px;align-content:start}
.field{height:37px;border:1.5px solid #999;border-radius:19px;font-size:10px;color:#555;padding:11px 18px}
.next{justify-self:end;width:95px;height:37px;background:var(--gold-dark);border-radius:19px;color:#fff;font-size:12px;font-weight:700;display:flex;align-items:center;justify-content:center;gap:10px}

/* testimonials */
.testi{position:absolute;top:2753px;left:0;width:1200px;height:453px}
.quote{position:absolute;top:173px;width:253px;height:222px;border:1.5px solid #777;border-radius:12px;padding:22px 28px}
.quote .mark{font-family:"Montserrat",sans-serif;font-size:32px;line-height:20px;color:var(--gold);font-weight:800}
.stars{color:var(--gold);font-size:14px;letter-spacing:2px;margin:6px 0 8px}
.quote p{font-size:11px;line-height:15px;color:#333}
.quote b{display:block;margin-top:10px;font-size:10px;color:#111}
.arrow{position:absolute;top:270px}

/* footer */
.footer{position:absolute;top:3206px;left:0;width:1200px;height:427px;background:var(--night);color:#ddd}
.perk{position:absolute;top:15px;width:266px;height:103px;border-radius:3px;padding:16px 17px;font-size:9.5px;color:#ddd}
.perk h4{font-family:"Figtree",sans-serif;font-size:15px;font-weight:600;color:#fff;margin-bottom:20px}
.perk a{display:block;color:#8c9cf0;margin-top:6px;text-decoration:none}
.perk .ico{position:absolute;right:15px;top:16px}
.col{position:absolute;top:148px;font-size:8.5px;line-height:16.3px;color:#eee}
.col .head{color:#aaa;font-size:7.5px}
.hours{position:absolute;left:848px;top:148px;width:152px;height:34px;border:1px solid #888;border-radius:4px;font-size:9.5px;line-height:11px;color:#fff;padding:6px 8px;font-weight:600}
.creed{position:absolute;left:848px;top:192px;width:160px;font-size:9.5px;line-height:11px;color:#eee;font-weight:600}
.news{position:absolute;top:376px;left:300px;width:300px;font-size:9px;text-align:center;line-height:11px}
.news-in{position:absolute;left:699px;top:377px;width:155px;height:22px;border:1px solid #ccc;background:#fff;font-size:8px;color:#aaa;padding:5px 8px}
.news-btn{position:absolute;left:861px;top:377px;width:24px;height:24px;background:var(--navy);border-radius:3px;display:grid;place-items:center}

.contact{position:absolute;top:3633px;left:0;width:1200px;height:48px;background:linear-gradient(180deg,#fff,#e6e6e6);display:flex;justify-content:space-around;align-items:center;padding:0 150px;font-size:13px;color:#222;text-align:center;line-height:13px}
.base{position:absolute;top:3681px;left:0;width:1200px;height:119px;background:var(--night-2);color:#ddd}
.social{position:absolute;left:192px;top:15px;display:flex;align-items:center;gap:10px;font-size:9px}
.social i{width:15px;height:15px;border-radius:50%;background:#fff;display:inline-block}
.copyr{position:absolute;left:192px;top:48px;font-size:9px}
.sign{position:absolute;left:192px;top:75px;display:flex;align-items:center;gap:14px;font-size:24px;letter-spacing:.6px;color:#fff;text-transform:uppercase}
.sign i{width:34px;height:34px;border:2px solid #fff;border-radius:50%}
</style>
</head>
<body>

<div class="ticker">
  <span><b>GOLD</b>$2,923.06<span class="chg">+1.42</span></span>
  <span><b>SILVER</b>$32.98<span class="chg down">-0.11</span></span>
  <span><b>PLATINUM</b>$998.99<span class="chg">+14.39</span></span>
  <span><b>PALLADIUM</b>$989.66<span class="chg">+10.86</span></span>
</div>

<header class="header">
  <div class="brand"><i></i>Steadfast Precious Metals Refineries</div>
  <div class="search">Search for products or categories...</div>
  <svg class="hicon" style="left:913px" width="17" height="17" viewBox="0 0 24 24" fill="none" stroke="#222" stroke-width="2"><circle cx="12" cy="12" r="10"/><circle cx="12" cy="10" r="3"/><path d="M6 19c2-3 10-3 12 0"/></svg>
  <svg class="hicon" style="left:948px" width="15" height="17" viewBox="0 0 24 24" fill="#222"><path d="M12 2a7 7 0 0 0-7 7c0 5 7 13 7 13s7-8 7-13a7 7 0 0 0-7-7zm0 9.5a2.5 2.5 0 1 1 0-5 2.5 2.5 0 0 1 0 5z"/></svg>
  <div class="call"><svg width="16" height="16" viewBox="0 0 24 24" fill="#fff"><path d="M6.6 10.8a15 15 0 0 0 6.6 6.6l2.2-2.2c.3-.3.7-.4 1-.2 1.1.4 2.3.6 3.6.6.6 0 1 .4 1 1V20c0 .6-.4 1-1 1A17 17 0 0 1 3 4c0-.6.4-1 1-1h3.5c.6 0 1 .4 1 1 0 1.3.2 2.5.6 3.6.1.3 0 .7-.2 1z"/></svg></div>
</header>

<nav class="nav"><span>Gold</span><span>Silver</span><span>Shop All</span><span>Deals<sup>●</sup></span><span>Sell to us</span><span>We Buy</span><span>IRA</span><span>Jewelry</span></nav>

<section class="hero" role="img" aria-label="Refiner pouring molten gold from a glowing crucible">
  <div class="rule" style="top:119px;left:355px"></div>
  <h1 style="top:135px">REFINERY PROCESS</h1>
  <div class="rule" style="top:199px"></div>
</section>

<section class="trust">
  <h2>YOUR MOST<br>TRUSTED <span class="gold">GOLD<br>BUYER</span></h2>
  <div class="divider"></div>
  <div class="badge" style="left:410px"><div class="shape"></div>$250,000,000+<small>bought &amp; sold</small></div>
  <div class="badge" style="left:538px"><div class="shape"></div>$250,000,000+<small>bought &amp; sold</small></div>
  <div class="badge" style="left:662px"><div class="shape"></div>4.8/5 stars<small>1,000+ client reviews</small></div>
  <div class="badge" style="left:783px"><div class="shape" style="border-radius:50%"></div>12+ years<small>in business</small></div>
  <div class="badge" style="left:905px"><div class="square"></div><small style="font-size:7px;color:#222;font-weight:600">Click for Profile</small>A+ rating</div>
</section>

<section class="about">
  <div class="video" role="img" aria-label="Video: a tour of our precious metal refinery"><div class="play"><svg width="22" height="24" viewBox="0 0 22 24"><path d="M3 2l17 10L3 22z" fill="#fff"/></svg></div></div>
  <div class="copy">
    <h2 class="eyebrow">ABOUT OUR</h2>
    <h2 class="big gold">PRECIOUS METAL<br>REFINERY</h2>
    <span class="flourish" role="img" aria-label="Ornamental flourish" style="margin:20px 0 28px"></span>
    <p>Most refineries are set up to work on precious metals behind closed doors. Here at Steadfast KLV we not only invite you to witness your lot being melted; we encourage you to watch every step of your metals being processed. We have a comfortable waiting area with bulletproof walls and windows for you to witness the melting as it is taking place.</p>
    <p>Our precious metal refinery is equipped with the latest technology and state of the art assaying equipment used to test each lot of your precious metals, ensuring your results are both accurate and precise.</p>
    <p>You will receive an analysis of your metals; certifying the results and giving you peace of mind.</p>
    <p>We take pride in our timeliness and efficiency. We know that time is money and your time is valuable; we will give you your one-day settlement in a matter of hours, with your choice of cash, check or wire transfer. Please call ahead and schedule a same-day appointment at our facility.</p>
  </div>
</section>

<section class="values">
  <article class="card" style="left:196px">
    <div class="photo" role="img" aria-label="Gold jewelry melting in a crucible" style="background:linear-gradient(150deg,#9a9a9a,#5e5e5e 45%,#d9541c 75%,#c9a233)"></div>
    <h3>OPTIMIZE YOUR<br>EARNINGS</h3>
    <span class="flourish" role="img" aria-label="Ornamental flourish"></span>
    <p>You are able to receive the most cash for your silver through us. Why? Because we are the refinery! This allows us to give you the most money. No need to go through cash for gold places or pawn shops, our in-house refinery gives you direct access to those savings.</p>
  </article>
  <article class="card" style="left:475px">
    <div class="photo" role="img" aria-label="Refiner at work beside the furnace" style="background:linear-gradient(150deg,#d8d8d8,#8a8a8a 50%,#3a3a3a 80%,#d8621e)"></div>
    <h3>NO MIDDLE-MAN</h3>
    <span class="flourish" role="img" aria-label="Ornamental flourish"></span>
    <p style="text-align:center">At Steadfast Precious Metals we melt gold and silver received from buying gold and authorized dealers such as pawn shops and we buy gold places. Doesn't it make sense to cut them out? Deal direct with us, we're confident you'll walk out happy!</p>
  </article>
  <article class="card" style="left:755px">
    <div class="photo" role="img" aria-label="Molten gold poured into a bar mold" style="background:linear-gradient(160deg,#3a3a3a,#6b4a30 35%,#f08a26 65%,#f5b23a)"></div>
    <h3>TRUST &amp; REPUTATION</h3>
    <span class="flourish" role="img" aria-label="Ornamental flourish"></span>
    <p>Dealing direct also gives you access to our resources, industry standard technology allowing us to treat your items with the utmost care. Our process is risk-free as we maintain the integrity of your jewelry through our non-invasive process whether or not you decide to sell.</p>
  </article>
</section>

<section class="rel">
  <div class="copy">
    <h2 class="eyebrow">PERSONAL</h2>
    <h2 class="big gold">RELATIONSHIPS</h2>
    <span class="flourish" role="img" aria-label="Ornamental flourish" style="margin:20px 0 28px"></span>
    <p>We at Steadfast Precious Metals Refineries recognize the value of personal relationships and the details that take service from good to great. We strive to build a personal relationship with our clients. By gaining your confidence and giving consistent accurate results, we work diligently to earn your trust. Ensuring our client's complete satisfaction is our number one goal.</p>
    <p>Steadfast Precious Metals Refineries is built on the idea that trust is the most important asset to a successful business. We strive to earn your trust and confidence every day through transparency, accuracy and personal relationships with each and every client. We recognize that trust is valuable and we at Steadfast KLV want to earn yours.</p>
    <p>Trust can only be earned; give us the opportunity to serve you.</p>
  </div>
  <div class="frame" role="img" aria-label="Image placeholder: our team meeting a client"></div>
</section>

<section class="reg">
  <h2 class="center-title" style="margin-top:48px">WHOLESALE <span class="gold">REGISTRATION</span></h2>
  <span class="flourish" role="img" aria-label="Ornamental flourish"></span>
  <div class="tabs">
    <div class="tab active" style="width:171px"><svg width="20" height="15" viewBox="0 0 20 15"><rect x="1" y="1" width="18" height="13" rx="2" fill="none" stroke="#fff" stroke-width="1.6"/><circle cx="6" cy="6" r="2" fill="#fff"/><path d="M10 5h6M10 8h6M3 11h6" stroke="#fff" stroke-width="1.4"/></svg>Business Contact<br>Information</div>
    <div class="tab" style="width:158px"><svg width="16" height="16" viewBox="0 0 16 16"><rect x="1" y="1" width="14" height="14" rx="2" fill="#333"/><circle cx="8" cy="6" r="2.5" fill="#fff"/><path d="M3.5 13c1-3 8-3 9 0" fill="#fff"/></svg>Primary Owner<br>or Principal</div>
    <div class="tab" style="width:158px"><svg width="18" height="16" viewBox="0 0 18 16"><circle cx="6" cy="4" r="3" fill="#333"/><path d="M0 15c0-5 12-5 12 0z" fill="#333"/><path d="M12 6h5M12 9h5M12 12h5" stroke="#333" stroke-width="1.6"/></svg>Secondary Owner<br>or Principal</div>
    <div class="tab" style="width:109px"><svg width="16" height="16" viewBox="0 0 16 16"><rect x="2" y="1" width="11" height="14" rx="1" fill="#333"/><path d="M4 5h7M4 8h7M4 11h5" stroke="#fff" stroke-width="1.3"/></svg>Billing</div>
    <div class="tab" style="width:124px"><svg width="22" height="14" viewBox="0 0 22 14"><rect x="0" y="1" width="13" height="9" fill="#333"/><path d="M13 4h5l3 3v3h-8z" fill="#333"/><circle cx="4" cy="11.5" r="2" fill="#333"/><circle cx="17" cy="11.5" r="2" fill="#333"/></svg>Shipping</div>
  </div>
  <form class="form">
    <div class="field">Lega Business Name*</div><div class="field">Company Phone*</div><div class="field">Email*</div>
    <div class="field">Company Physical Address*</div><div class="field">City*</div><div class="field">State*</div>
    <div class="field">Zip*</div><div class="field">Federal ID/EIN*</div><div class="field">Date Business Commenced*</div>
    <div class="field">Business Type*</div><div class="field">Website</div><div class="next">NEXT <svg width="6" height="10" viewBox="0 0 6 10"><path d="M1 1l4 4-4 4" stroke="#fff" fill="none" stroke-width="1.4"/></svg></div>
  </form>
</section>

<section class="testi">
  <h2 class="center-title" style="margin-top:56px">TESTIMONIALS</h2>
  <span class="flourish" role="img" aria-label="Ornamental flourish"></span>
  <svg class="arrow" style="left:131px" width="16" height="28" viewBox="0 0 16 28"><path d="M14 2L3 14l11 12" stroke="#999" stroke-width="2.5" fill="none"/></svg>
  <svg class="arrow" style="left:1053px" width="16" height="28" viewBox="0 0 16 28"><path d="M2 2l11 12L2 26" stroke="#999" stroke-width="2.5" fill="none"/></svg>
  <article class="quote" style="left:195px"><div class="mark">“</div><div class="stars">★★★★★</div><p>Lorem ipsum dolor sit amet, consectetur adipiscing elit, sed do eiusmod tempor incididunt ut labore et dolore magna aliqua. Ut enim ad minim veniam, quis nostrud exercitation ullamco laboris nisi ut aliquip ex ea commodo consequat. Duis aute irure dolor in.</p><b>ELLIS BRANDT</b></article>
  <article class="quote" style="left:472px"><div class="mark">“</div><div class="stars">★★★★★</div><p>Lorem ipsum dolor sit amet, consectetur adipiscing elit, sed do eiusmod tempor incididunt ut labore et dolore magna aliqua. Ut enim ad minim veniam, quis nostrud exercitation ullamco laboris nisi ut aliquip ex ea commodo consequat. Duis aute irure dolor in.</p><b>ELLIS BRANDT</b></article>
  <article class="quote" style="left:753px"><div class="mark">“</div><div class="stars">★★★★★</div><p>Lorem ipsum dolor sit amet, consectetur adipiscing elit, sed do eiusmod tempor incididunt ut labore et dolore magna aliqua. Ut enim ad minim veniam, quis nostrud exercitation ullamco laboris nisi ut aliquip ex ea commodo consequat. Duis aute irure dolor in.</p><b>ELLIS BRANDT</b></article>
</section>

<footer class="footer">
  <div class="perk" style="left:192px;background:linear-gradient(135deg,#3a3a3a,#242424);border:1px solid #555">
    <h4>Price match guarantee</h4>
    <svg class="ico" width="14" height="14" viewBox="0 0 14 14"><circle cx="7" cy="7" r="6" fill="none" stroke="#aaa"/><path d="M4 7l2 2 4-4" stroke="#aaa" fill="none"/></svg>
    on all bullion products.<a>Learn more</a>
  </div>
  <div class="perk" style="left:466px;background:linear-gradient(135deg,#1e2a7a,#1a1f45)">
    <h4>100% Insured</h4>
    <svg class="ico" width="13" height="15" viewBox="0 0 13 15"><path d="M6.5 1L12 3v4c0 4-3 6-5.5 7C4 13 1 11 1 7V3z" fill="none" stroke="#aab"/></svg>
    <div style="margin-top:34px">All orders are tracked and insured.</div>
  </div>
  <div class="perk" style="left:741px;background:linear-gradient(135deg,#2e2a1e,#6b5a22 55%,#b0952e)">
    <h4 style="margin-bottom:10px">Free Shipping</h4>
    <svg class="ico" width="17" height="12" viewBox="0 0 17 12"><rect x="1" y="1" width="10" height="7" fill="none" stroke="#ccc"/><path d="M11 3h3l2 3v2h-5" fill="none" stroke="#ccc"/></svg>
    Orders ship free over $499.<div style="font-size:5px;margin-top:3px">*some limits apply</div><a>Shop now</a>
  </div>

  <div class="col" style="left:199px"><div class="head">Buying &amp; selling</div>Shop Bullion<br>IRA Rollovers<br>Silver Bullion<br>Gold Bullion<br>Platinum Bullion<br>Palladium Bullion<br>Steadfast Jewelry</div>
  <div class="col" style="left:361px"><div class="head">Company</div>Leave a Review<br>Testimonials<br>Refinery Process<br>Blog<br>About Us</div>
  <div class="col" style="left:523px"><div class="head">Customer care</div>My account<br>Investment Tools<br>Contact us<br>FAQs<br>Jewelry 101<br>Jewelry Repair</div>
  <div class="col" style="left:685px"><div class="head">Legal</div>Privacy Policy<br>Terms and Conditions<br>Mail-in Terms<br>Acceptable Use<br>Cookie Policy<br>Disclaimer Policy<br>Payment Terms<br>Shipping Policy<br>Returns Policy<br>Price Match<br>Affiliate Program Terms of Use</div>
  <div class="hours">Open Mon-Fri<br>10:00a - 6:00p PST</div>
  <div class="creed">Steadfast Precious Metals Refineries is a proudly patriotic Christian business in the United States of America.
    <div style="margin-top:8px;display:flex;gap:14px;align-items:center">
      <svg width="12" height="18" viewBox="0 0 12 18"><path d="M6 0v18M1 5h10" stroke="#fff" stroke-width="2.4"/></svg>
      <svg width="38" height="20" viewBox="0 0 38 20" role="img" aria-label="United States flag"><rect width="38" height="20" fill="#c8283c"/><path d="M0 4h38M0 8h38M0 12h38M0 16h38" stroke="#fff" stroke-width="1.5"/><rect width="16" height="11" fill="#2a3b8f"/></svg>
    </div>
  </div>
  <div class="news">Subscribe to our newsletter to be the first to know about special deals and promotions.</div>
  <div class="news-in">Enter Email</div>
  <div class="news-btn"><svg width="12" height="9" viewBox="0 0 12 9"><rect width="12" height="9" fill="#fff"/><path d="M0 0l6 5 6-5" stroke="#1f2a6b" fill="none"/></svg></div>
</footer>

<div class="contact"><span>(503) 555-0148</span><span>2210 Linden Row NE,<br>Marlow, OR 97390</span><span>info@steadfastklv.com</span></div>

<div class="base">
  <div class="social">Follow us on social media to stay up to date: <i></i><i></i><i></i><i></i><i></i></div>
  <div class="copyr">© 2025 All Rights Reserved Steadfast Precious Metals Refineries</div>
  <div class="sign"><i></i>Steadfast Precious Metals Refineries</div>
</div>

</body>
</html>
```